Art for parenting podcast with straight/direct talk...no fluff here! "Clear Ground for Families"

I need an image that will not look fluffy or soft. A no-nonsense look. This is not a 'I love parenting' podcast. It is for frustrated parents who don't know what to do. The name is 'Clear Ground for Families'. The design should, therefore, NOT have hearts and flowers but, instead, look clean and direct. My logo has shades of blue so that would be nice. I have done this work for over 30 years and am well-degreed so would like the design to look stable/established. I have attached my company's logo.

Target Market(s)

Frustrated parents of children - age birth to 20

Industry/Entity Type

Coaching/Counseling for parents

Font styles to use
Serif
Sans Serif

Colors
0054AA
0677BA
7BADD7
CADEEF
E8F1F8

Requirements
Must have
• A look that is clean/bold/direct and professional. Serious.
Nice to have
• If it looks good, my name with my degrees behind my name. MS, MEd. Another thought would be to have a background image of a frustrated parent. Not sure if that would be good or look too busy.
Should not have
• Flowers, fluff, soft appearance, pinks, light colors

```html
<!DOCTYPE html>
<html lang="en">
<head>
<meta charset="utf-8">
<title>Clear Ground for Families – Podcast Cover</title>
<link rel="stylesheet" href="https://fonts.googleapis.com/css2?family=Bebas+Neue&family=Oswald:wght@500&display=swap">
<style>
  :root {
    --stage: #e4e5e7;
    --blue-deep: #0054aa;
    --blue-mid: #0677ba;
    --blue-soft: #7badd7;
    --blue-pale: #cadeef;
    --blue-mist: #e8f1f8;
    --navy: #10163f;
    --white: #ffffff;
  }
  * { margin: 0; padding: 0; box-sizing: border-box; }
  html, body {
    width: 1200px;
    height: 807px;
    overflow: hidden;
    background: var(--stage);
  }
  .cover {
    position: absolute;
    left: 250px;
    top: 53px;
    width: 700px;
    height: 700px;
    overflow: hidden;
    background:
      radial-gradient(circle at 78% 62%, var(--blue-soft) 0%, var(--blue-mid) 30%, var(--blue-deep) 72%);
    box-shadow: 0 24px 30px -18px rgba(0, 0, 0, 0.35);
  }
  .cover__frame {
    position: absolute;
    inset: 20px;
    border: 3px solid var(--white);
    pointer-events: none;
    z-index: 3;
  }
  .cover__figure {
    position: absolute;
    right: 40px;
    bottom: 23px;
    width: 230px;
    height: 380px;
    border-radius: 48% 52% 0 0 / 30% 30% 0 0;
    background: linear-gradient(180deg, #1a2566 0%, var(--navy) 70%);
    z-index: 1;
  }
  .title {
    position: absolute;
    left: 58px;
    top: 82px;
    z-index: 2;
    font-family: "Bebas Neue", "Oswald", sans-serif;
    font-size: 146px;
    line-height: 0.8;
    color: var(--white);
    letter-spacing: 1px;
  }
  .title__line { display: block; height: 118px; }
  .title__line--accent { color: var(--blue-pale); display: flex; align-items: flex-start; gap: 16px; }
  .title__badge {
    display: inline-flex;
    align-items: center;
    justify-content: center;
    width: 108px;
    height: 108px;
    margin-top: -4px;
    border-radius: 50%;
    background: var(--white);
    color: var(--blue-deep);
    font-size: 58px;
    line-height: 1;
    padding-top: 6px;
  }
  .byline {
    position: absolute;
    left: 62px;
    top: 458px;
    z-index: 2;
    font-family: "Oswald", sans-serif;
    font-weight: 500;
    font-size: 25px;
    color: var(--white);
    letter-spacing: 0.3px;
  }
  .brand {
    position: absolute;
    left: 84px;
    top: 578px;
    z-index: 2;
    display: flex;
    align-items: center;
    gap: 12px;
    font-family: "Oswald", sans-serif;
    font-weight: 500;
    font-size: 26px;
    color: var(--white);
    letter-spacing: 1px;
  }
  .brand__dot {
    width: 34px;
    height: 34px;
    border-radius: 50%;
    background: var(--white);
  }
</style>
</head>
<body>
  <main class="cover">
    <div class="cover__frame"></div>
    <div class="cover__figure" role="img" aria-label="Dark silhouette of a frustrated parent holding their head in their hands"></div>
    <h1 class="title">
      <span class="title__line">Clear</span>
      <span class="title__line title__line--accent">Ground <span class="title__badge">For</span></span>
      <span class="title__line">Families</span>
    </h1>
    <p class="byline">BY DANA WHITCOMBE, MS, MED</p>
    <div class="brand">
      <span class="brand__dot"></span>
      <span class="brand__name">NORTHLINE PARENTING</span>
    </div>
  </main>
</body>
</html>
```